Still Harbor website development

Need a website designed for a coaching business. Very high-end, luxury, professionalism, in the area of STRESS, see brief attached. I have a logo already
Updates

Slow in providing feedback

Target Market(s)

CEOs very successful men and wealthy females, high end luxury market

Industry/Entity Type

coaching

Number of Pages Required

1 page

Requirements
Must have
• Luxury look, professional, serious but warm, appealing to both sexes

```html
<!DOCTYPE html>
<html lang="en">
<head>
<meta charset="utf-8">
<title>Still Harbor — Lifestyle Coaching</title>
<link href="https://fonts.googleapis.com/css2?family=Roboto+Condensed:wght@400;700&family=Lato:wght@400;700&display=swap" rel="stylesheet">
<style>
:root{
  --blue:#1a4fa3;
  --blue-deep:#123c82;
  --gold:#d4970f;
  --ink:#1b1b1b;
  --text:#2f2f2f;
  --muted:#5b5b5b;
  --night:#07080c;
  --line:#cfd6e2;
  --white:#ffffff;
}
*{box-sizing:border-box;margin:0;padding:0}
html,body{width:1200px;height:3810px;overflow:hidden;background:var(--white)}
body{position:relative;font-family:"Lato",sans-serif;color:var(--text)}
.abs{position:absolute}
.head-font{font-family:"Roboto Condensed",sans-serif;font-weight:700;text-transform:uppercase;color:var(--ink)}
.btn{position:absolute;display:flex;align-items:center;justify-content:center;gap:10px;font-family:"Roboto Condensed",sans-serif;font-weight:700;font-size:16px;color:#fff;text-transform:uppercase;box-shadow:0 3px 8px rgba(0,0,0,.18)}
.btn .dot{width:15px;height:15px;border-radius:50%;background:#fff;display:inline-flex;align-items:center;justify-content:center}
.btn .dot svg{width:9px;height:9px}
.btn-gold{background:var(--gold)}
.btn-blue{background:var(--blue)}

/* header */
.site-header{position:absolute;left:0;top:0;width:1200px;height:71px;background:#fff;z-index:5}
.brand-box{position:absolute;left:118px;top:0;width:168px;height:106px;background:#fff;box-shadow:0 4px 10px rgba(0,0,0,.12);z-index:6;display:flex;flex-direction:column;align-items:center;justify-content:center;gap:6px}
.brand-box .mark{width:30px;height:30px;background:var(--ink)}
.brand-box .name{font-family:"Roboto Condensed",sans-serif;font-weight:700;font-size:14px;letter-spacing:2px;color:var(--ink)}
.nav{position:absolute;top:24px;font-family:"Roboto Condensed",sans-serif;font-size:15px;color:#222;text-transform:uppercase}
.nav.active{color:var(--gold)}
.phone-ic{position:absolute;left:783px;top:15px;width:37px;height:37px;border-radius:50%;background:var(--blue);display:flex;align-items:center;justify-content:center}
.phone-txt{position:absolute;left:833px;top:23px;font-family:"Roboto Condensed",sans-serif;font-size:16px;color:#222}

/* hero */
.hero-photo{position:absolute;left:0;top:71px;width:1200px;height:632px;background:linear-gradient(180deg,#57709a 0%,#c39368 38%,#6c5a4c 60%,#4b3f35 100%);clip-path:polygon(0 0,100% 0,100% 88%,86% 99%,50% 75%,14.6% 99%,0 77%)}
.hero-lines{position:absolute;left:0;top:71px}
.hero-title{left:108px;top:243px;font-size:60px;color:#fff;line-height:1}
.hero-sub{left:111px;top:322px;width:380px;font-size:18px;line-height:28px;color:#f2ece6}
.slides{left:1112px;top:302px;font-family:"Roboto Condensed",sans-serif;font-weight:700;font-size:20px;line-height:39px;color:#fff}
.slides .on{color:var(--gold)}
.hex-deco{left:0;top:651px;width:150px;height:430px;background:linear-gradient(90deg,#e6eef9,rgba(230,238,249,0))}

/* welcome */
.section-title{position:absolute;left:0;width:1200px;text-align:center;font-size:33px}
.welcome-body{position:absolute;left:180px;top:808px;width:840px}
.welcome-body p{text-align:center;font-size:15px;line-height:26.6px;color:var(--text)}
.welcome-body p + p{margin-top:14px}

/* why me */
.why-photo{left:0;top:1188px;width:595px;height:437px;background:linear-gradient(135deg,#7d7c78,#b9b3aa 45%,#6d7a86)}
.why-panel{left:595px;top:1188px;width:605px;height:437px;background:var(--blue)}
.why-title{left:654px;top:1243px;font-size:33px;color:#fff}
.why-item{left:694px;width:458px;font-size:14.5px;line-height:25.7px;color:#eaf0fb}
.why-tick{left:654px;width:16px;height:16px;border-radius:50%;background:var(--gold);display:flex;align-items:center;justify-content:center}

/* benefits */
.card{position:absolute;top:1783px;width:232px;height:321px;background:#fff;border:1px solid #e2e2e2}
.card .img{height:150px}
.card .body{padding:17px 12px 0 16px}
.card p{font-size:12.3px;line-height:21.5px;color:#333}
.card a{display:inline-block;margin-top:4px;font-family:"Roboto Condensed",sans-serif;font-weight:700;font-size:13px;color:var(--blue);text-decoration:underline}
.arrow{position:absolute;top:1930px}

/* blog */
.blog-band{left:0;top:2190px;width:1200px;height:621px;background:linear-gradient(180deg,#1c56ad,#194b99)}
.post{position:absolute;top:2313px;height:444px;background:#fff}
.post .tag{position:absolute;background:var(--gold);color:#fff;font-size:12px;border-radius:10px;padding:3px 26px;text-transform:uppercase}
.post h3{position:absolute;left:33px;font-family:"Roboto Condensed",sans-serif;font-weight:700;font-size:16px;color:var(--ink)}
.post p{position:absolute;left:33px;font-size:14.5px;line-height:26px;color:#6a6a6a}
.post .meta{position:absolute;left:26px;bottom:0;height:48px;border-top:1px solid #eee;display:flex;align-items:center;gap:14px;font-family:"Roboto Condensed",sans-serif;font-size:15px;letter-spacing:1px;color:#444;text-transform:uppercase}
.post .avatar{width:26px;height:26px;border-radius:50%;background:#9fb2c9}
.post .plus{position:absolute;width:32px;height:32px;border-radius:50%;background:var(--gold);color:#fff;font-size:24px;line-height:31px;text-align:center}

/* contact */
.contact-bg{left:0;top:2811px;width:1200px;height:660px;background:linear-gradient(180deg,#f4f6fa,#e8edf4)}
.field{position:absolute;border-bottom:1.5px solid var(--blue);height:44px;font-size:14px;color:#222;padding-top:4px}

/* footer */
.footer-bg{left:0;top:3300px;width:1200px;height:510px}
.f-head{font-family:"Roboto Condensed",sans-serif;font-weight:700;font-size:14px;color:#fff;text-transform:uppercase}
.f-text{font-size:14.5px;line-height:21px;color:#e8e8e8}
.f-ic{left:450px;width:16px;height:16px}
.social{top:3674px;width:38px;height:38px;border-radius:50%;background:var(--blue)}
</style>
</head>
<body>

<header class="site-header">
  <span class="nav active" style="left:312px">Home</span>
  <span class="nav" style="left:376px">Why Me</span>
  <span class="nav" style="left:452px">Benefits</span>
  <span class="nav" style="left:537px">Target Audience</span>
  <span class="nav" style="left:678px">Contact Us</span>
  <span class="phone-ic"><svg width="16" height="16" viewBox="0 0 24 24"><path fill="#fff" d="M6.6 10.8a15 15 0 0 0 6.6 6.6l2.2-2.2c.3-.3.7-.4 1-.2 1.1.4 2.3.6 3.6.6.6 0 1 .4 1 1V20c0 .6-.4 1-1 1A17 17 0 0 1 3 4c0-.6.4-1 1-1h3.5c.6 0 1 .4 1 1 0 1.3.2 2.5.6 3.6.1.3 0 .7-.2 1z"/></svg></span>
  <span class="phone-txt">+1 555 010 2040</span>
  <span class="btn btn-gold" style="left:975px;top:13px;width:107px;height:40px">Login <span class="dot"><svg viewBox="0 0 10 10"><path d="M3 1.5 7 5 3 8.5" stroke="#d4970f" stroke-width="2" fill="none"/></svg></span></span>
</header>
<div class="brand-box"><span class="mark"></span><span class="name">STILL HARBOR</span></div>

<div class="hero-photo" role="img" aria-label="Woman stretching on a wooden jetty by a lake at sunset, swan on the water"></div>
<svg class="hero-lines" width="1200" height="640" viewBox="0 0 1200 640"><polyline points="175,630 600,474 1028,630" fill="none" stroke="#1a4fa3" stroke-width="8"/></svg>
<h1 class="abs head-font hero-title">Head Coach</h1>
<p class="abs hero-sub">Still Harbor came about due to my desire to help people lead a better and healthier life.</p>
<span class="btn btn-gold" style="left:111px;top:401px;width:142px;height:47px">Women <span class="dot"><svg viewBox="0 0 10 10"><path d="M3 1.5 7 5 3 8.5" stroke="#d4970f" stroke-width="2" fill="none"/></svg></span></span>
<span class="btn btn-blue" style="left:257px;top:401px;width:142px;height:47px">Men <span class="dot"><svg viewBox="0 0 10 10"><path d="M3 1.5 7 5 3 8.5" stroke="#1a4fa3" stroke-width="2" fill="none"/></svg></span></span>
<div class="abs slides"><div>01</div><div class="on">02</div><div>03</div></div>

<div class="abs hex-deco" role="img" aria-label="Faint hexagon pattern decoration"></div>
<section class="welcome">
  <h2 class="section-title head-font" style="top:757px">Welcome to StillHarbor</h2>
  <div class="welcome-body">
    <p>Still Harbor came about due to my desire to help people lead a better and healthier life. Initially, I was involved in the fitness/body side of health. As years passed and my experience grew, I realized how important the mind was in total wellness, and that the mind is all powerful and controlling. Control the mind, control the body and achieve success. Stress can be the most debilating factor in our lives, it is the root cause of so many diseases and costs the US workplace an estimated 300 billion dollars due to loss of productivity.</p>
    <p>tress is not all bad, and since we are surrounded by engulfed by stress, or it isn't going anywhere soon, weneed to deal with it, and even better, channel to be an advantage/tool to perform better.Recognize when we are feeling stress and what is causing it, understand it, and how we react to it is the first step.</p>
  </div>
  <span class="btn btn-gold" style="left:521px;top:1056px;width:157px;height:46px">Learn More <span class="dot"><svg viewBox="0 0 10 10"><path d="M3 1.5 7 5 3 8.5" stroke="#d4970f" stroke-width="2" fill="none"/></svg></span></span>
</section>

<div class="abs why-photo" role="img" aria-label="Smiling woman holding a white mug in a bright studio"></div>
<div class="abs why-panel"></div>
<h2 class="abs head-font why-title">Why Me</h2>
<span class="abs why-tick" style="top:1349px"><svg width="9" height="9" viewBox="0 0 10 10"><path d="M1.5 5.2 4 7.5 8.5 2.5" stroke="#fff" stroke-width="1.8" fill="none"/></svg></span>
<p class="abs why-item" style="top:1305px">Been there done that! Have been through a lot, started businesses, selling a business, law suits, marriage, divorce, second marriage, kids, school, sports, fights, robbed, gun in face, traveled the world, successful, two great kids (both Cadets at Ridgefield Academy.duty/country)</p>
<span class="abs why-tick" style="top:1451px"><svg width="9" height="9" viewBox="0 0 10 10"><path d="M1.5 5.2 4 7.5 8.5 2.5" stroke="#fff" stroke-width="1.8" fill="none"/></svg></span>
<p class="abs why-item" style="top:1434px">Limited number of clients…different stage of life,empty neste, have a full career won't be a number</p>
<span class="btn btn-gold" style="left:654px;top:1517px;width:157px;height:44px">Learn More <span class="dot"><svg viewBox="0 0 10 10"><path d="M3 1.5 7 5 3 8.5" stroke="#d4970f" stroke-width="2" fill="none"/></svg></span></span>

<h2 class="section-title head-font" style="top:1702px">Our Benefits</h2>
<svg class="arrow" style="left:54px" width="16" height="24" viewBox="0 0 16 24"><path d="M12 3 4 12l8 9" stroke="#111" stroke-width="3" fill="none"/></svg>
<svg class="arrow" style="left:1130px" width="16" height="24" viewBox="0 0 16 24"><path d="M4 3l8 9-8 9" stroke="#111" stroke-width="3" fill="none"/></svg>
<article class="card" style="left:111px">
  <div class="img" role="img" aria-label="Relaxed woman at a desk with plants" style="background:linear-gradient(135deg,#c9c2b5,#d9a43f 55%,#6f8a5c)"></div>
  <div class="body">
    <p>Sector expert Health/Wellness. Presented at numerous industry shows and quoted in national publications (not as a coach, I'm new, but in the health &amp; wellness.</p>
    <a>READ MORE</a>
  </div>
</article>
<article class="card" style="left:359px">
  <div class="img" role="img" aria-label="Woman receiving a spa massage" style="background:linear-gradient(135deg,#d6b08c,#a86a45 55%,#f3ece2)"></div>
  <div class="body">
    <p>Excellent listener.being in sales for many years, the secret is to really listen…and get to the end game, and make it feel as if it was their decision. Not sure how to</p>
    <a>READ MORE</a>
  </div>
</article>
<article class="card" style="left:608px">
  <div class="img" role="img" aria-label="Group yoga class in a bright studio" style="background:linear-gradient(135deg,#3d4a42,#9aa69a 50%,#c9c4bd)"></div>
  <div class="body">
    <p>Access/resources industry professionals, sport psychologist. just spent a few hours with the Mind performance coach for the Bay City Hawks baseball team.</p>
    <a>READ MORE</a>
  </div>
</article>
<article class="card" style="left:856px">
  <div class="img" role="img" aria-label="Laughing couple outdoors in a city" style="background:linear-gradient(135deg,#52603d,#a58a6b 55%,#e4dccb)"></div>
  <div class="body">
    <p>Private, more than happy to sign confidentiality agreement. Especially for the business man</p>
    <a>READ MORE</a>
  </div>
</article>

<div class="abs blog-band"></div>
<h2 class="section-title head-font" style="top:2239px;color:#fff">Our Blog</h2>
<article class="post" style="left:112px;width:317px">
  <div role="img" aria-label="Person meditating on a hill above misty mountains" style="height:237px;background:linear-gradient(180deg,#9fc3de,#6f9a55 60%,#3e6b2d)"></div>
  <span class="tag" style="left:36px;top:226px">Lorem</span>
  <h3 style="top:270px">Lorem ipsum dolor sit consectetur</h3>
  <p style="top:300px;width:270px">Lorem ipsum dolor sit aconsectetur adipiscing elitsed eiusmod tempor incididunt onsectetur adipiscingdolore</p>
  <span class="plus" style="left:274px;top:378px">+</span>
  <div class="meta" style="width:291px"><span class="avatar" role="img" aria-label="Author portrait"></span>By: Admin &nbsp;|&nbsp; 12-Feb-2022</div>
</article>
<article class="post" style="left:451px;width:637px">
  <div role="img" aria-label="Smiling woman relaxing on a sofa" style="height:252px;background:linear-gradient(135deg,#c7d2df,#e9e4de 50%,#9aa8b8)"></div>
  <span class="tag" style="left:35px;top:240px">Lorem</span>
  <h3 style="top:267px">Lorem ipsum dolor sit amet, consectetur adipiscing elit</h3>
  <p style="top:296px;width:520px">Lorem ipsum dolor sit amet, consectetur adipiscing elitsed eiusmod tempor incididunt onsectetur adipiscingdolore magna aliquadolor sed consectetur. Lorem ipsum dolor sit adipiscing elitsed eiusmod tempor incididunt.</p>
  <div class="abs" style="left:570px;top:300px;width:36px;height:84px;border-radius:18px;background:#f1f2f4;display:flex;flex-direction:column;align-items:center;justify-content:center;gap:13px">
    <span style="width:8px;height:8px;border-radius:50%;background:#b9bec6"></span>
    <span style="width:8px;height:8px;border-radius:50%;background:#b9bec6"></span>
    <span style="width:8px;height:8px;border-radius:50%;background:#b9bec6"></span>
  </div>
  <span class="plus" style="left:571px;top:378px">+</span>
  <div class="meta" style="width:586px"><span class="avatar" role="img" aria-label="Author portrait"></span>By: Admin &nbsp;|&nbsp; 12-Feb-2022</div>
</article>

<div class="abs contact-bg" role="img" aria-label="Faded photo of a smiling woman"></div>
<h2 class="section-title head-font" style="top:2892px">Contact Us</h2>
<form>
  <div class="field" style="left:139px;top:2958px;width:430px">First Name:</div>
  <div class="field" style="left:630px;top:2958px;width:430px">Last Name:</div>
  <div class="field" style="left:139px;top:3035px;width:430px">Email:</div>
  <div class="field" style="left:630px;top:3035px;width:430px">Address:</div>
  <div class="field" style="left:139px;top:3112px;width:921px">Email:</div>
  <span class="btn btn-blue" style="left:528px;top:3204px;width:142px;height:47px">Submit <span class="dot"><svg viewBox="0 0 10 10"><path d="M3 1.5 7 5 3 8.5" stroke="#1a4fa3" stroke-width="2" fill="none"/></svg></span></span>
</form>

<svg class="abs footer-bg" width="1200" height="510" viewBox="0 0 1200 510">
  <polygon points="0,145 208,8 600,165 1028,8 1200,145 1200,510 0,510" fill="#07080c"/>
  <polyline points="208,8 600,165 1028,8" fill="none" stroke="#1a4fa3" stroke-width="8"/>
</svg>
<footer>
  <div class="abs" style="left:111px;top:3560px;width:252px;text-align:center">
    <span style="display:inline-block;width:60px;height:60px;background:#fff"></span>
    <div style="margin-top:28px;font-family:'Roboto Condensed',sans-serif;font-weight:700;font-size:30px;letter-spacing:5px;color:#fff">STILL HARBOR</div>
    <div style="margin-top:4px;font-family:'Roboto Condensed',sans-serif;font-weight:700;font-size:13px;letter-spacing:4px;color:#fff">LIFESTYLE COACHING</div>
  </div>

  <div class="abs f-head" style="left:450px;top:3524px">Contact Information</div>
  <svg class="abs f-ic" style="top:3570px" viewBox="0 0 16 16"><path d="M15 1 1 7l5 2 2 6z" fill="#fff"/></svg>
  <p class="abs f-text" style="left:488px;top:3563px;width:220px">Lorem ipsum dolor sit amet, consectetur adipiscing elit</p>
  <svg class="abs f-ic" style="top:3632px" viewBox="0 0 16 16"><rect x="1" y="3" width="14" height="10" fill="#fff"/><path d="M1 3l7 6 7-6" stroke="#07080c" stroke-width="1.3" fill="none"/></svg>
  <p class="abs f-text" style="left:488px;top:3628px">Email:hello@stillharbor.com</p>
  <svg class="abs f-ic" style="top:3674px" viewBox="0 0 24 24"><path fill="#fff" d="M6.6 10.8a15 15 0 0 0 6.6 6.6l2.2-2.2c.3-.3.7-.4 1-.2 1.1.4 2.3.6 3.6.6.6 0 1 .4 1 1V20c0 .6-.4 1-1 1A17 17 0 0 1 3 4c0-.6.4-1 1-1h3.5c.6 0 1 .4 1 1 0 1.3.2 2.5.6 3.6.1.3 0 .7-.2 1z"/></svg>
  <p class="abs f-text" style="left:488px;top:3672px">Phone: +1 555 010 2040</p>

  <div class="abs f-head" style="left:772px;top:3524px">Newsletter</div>
  <p class="abs f-text" style="left:772px;top:3560px">Enter your email &amp; subcribing newsletter</p>
  <div class="abs" style="left:772px;top:3603px;width:212px;height:43px;background:#1b1d24;display:flex;align-items:center;gap:12px;padding-left:14px;font-size:12.5px;color:#cfcfcf">
    <svg width="14" height="11" viewBox="0 0 14 11"><rect x=".7" y=".7" width="12.6" height="9.6" fill="none" stroke="#d4970f" stroke-width="1.3"/><path d="M1 1l6 5 6-5" stroke="#d4970f" stroke-width="1.3" fill="none"/></svg>Email address
  </div>
  <span class="abs" style="left:984px;top:3603px;width:107px;height:43px;background:var(--gold);color:#fff;font-family:'Roboto Condensed',sans-serif;font-weight:700;font-size:14px;display:flex;align-items:center;justify-content:center">SUBSCRIBE</span>
  <span class="abs social" style="left:771px"></span>
  <span class="abs social" style="left:814px"></span>
  <span class="abs social" style="left:857px"></span>
  <span class="abs social" style="left:900px"></span>

  <div class="abs" style="left:111px;top:3746px;width:978px;height:1px;background:#3a3d46"></div>
  <p class="abs" style="left:0;top:3767px;width:1200px;text-align:center;font-size:14.5px;color:#e8e8e8">2022 © Copyrights Still Harbor All rights reserved.</p>
</footer>
</body>
</html>
```